TALMORK

The business want a professional looking business card. We have a scetch we will add but want the extra upgrade, and would like more suggestions for variations of our business cards.

```html
<!DOCTYPE html>
<html lang="en">
<head>
<meta charset="utf-8">
<title>Talmork Business Card</title>
<link rel="stylesheet" href="https://fonts.googleapis.com/css2?family=Playfair+Display:ital,wght@0,700;1,800&family=Montserrat:wght@400;500&display=swap">
<style>
  :root {
    --backdrop: #4a4a4a;
    --card: #141414;
    --gold: #d9a93a;
    --gold-light: #f3d27a;
    --gold-dark: #8a6420;
    --white: #f2f2f2;
    --silver: #e4e4e4;
  }
  * { margin: 0; padding: 0; box-sizing: border-box; }
  html, body { width: 1200px; height: 800px; overflow: hidden; }
  body {
    background: var(--backdrop);
    position: relative;
    font-family: "Montserrat", sans-serif;
  }
  .card {
    position: absolute;
    background: var(--card);
    border-radius: 28px;
    border: 3px solid var(--gold);
    box-shadow: 0 18px 40px rgba(0,0,0,0.45);
  }
  .card-front {
    left: 80px; top: 90px;
    width: 380px; height: 620px;
    display: flex; flex-direction: column; align-items: center;
    padding-top: 120px;
    text-align: center;
  }
  .front-brand {
    font-family: "Playfair Display", serif;
    font-weight: 700;
    font-size: 46px;
    letter-spacing: 4px;
    color: var(--gold);
  }
  .front-brand-mark {
    width: 22px; height: 22px;
    border-radius: 50%;
    background: var(--gold);
    margin-bottom: 18px;
  }
  .holder-name {
    margin-top: 110px;
    font-family: "Playfair Display", serif;
    font-style: italic;
    font-weight: 800;
    font-size: 27px;
    color: var(--gold-light);
  }
  .holder-role {
    margin-top: 10px;
    font-size: 15px;
    color: var(--white);
    letter-spacing: 0.5px;
  }
  .contact-icons {
    margin-top: 22px;
    display: flex; gap: 12px;
  }
  .contact-icon {
    width: 26px; height: 26px;
    border-radius: 50%;
    background: var(--gold);
    display: flex; align-items: center; justify-content: center;
  }
  .contact-list {
    margin-top: 18px;
    list-style: none;
    font-size: 15px;
    line-height: 1.75;
    color: var(--white);
  }
  .card-back {
    left: 540px; top: 250px;
    width: 600px; height: 370px;
    display: flex; flex-direction: column; align-items: center; justify-content: center;
  }
  .back-brand {
    font-family: "Playfair Display", serif;
    font-weight: 700;
    font-size: 86px;
    letter-spacing: 6px;
    color: var(--silver);
  }
  .back-tagline {
    margin-top: 6px;
    font-size: 20px;
    font-weight: 500;
    letter-spacing: 16px;
    color: var(--silver);
    padding-left: 16px;
  }
</style>
</head>
<body>
  <section class="card card-front">
    <div class="front-brand-mark"></div>
    <div class="front-brand">TALMORK</div>
    <h1 class="holder-name">Anders Lund Vikhamar</h1>
    <p class="holder-role">CEO &amp; Founder</p>
    <div class="contact-icons">
      <span class="contact-icon" aria-label="Phone">
        <svg width="14" height="14" viewBox="0 0 24 24"><path d="M6.6 10.8a15 15 0 0 0 6.6 6.6l2.2-2.2a1 1 0 0 1 1-.25 11.4 11.4 0 0 0 3.6.57 1 1 0 0 1 1 1V20a1 1 0 0 1-1 1A17 17 0 0 1 3 4a1 1 0 0 1 1-1h3.5a1 1 0 0 1 1 1c0 1.25.2 2.45.57 3.6a1 1 0 0 1-.25 1z" fill="#141414"/></svg>
      </span>
      <span class="contact-icon" aria-label="Email">
        <svg width="14" height="14" viewBox="0 0 24 24"><rect x="3" y="6" width="18" height="12" rx="1" fill="none" stroke="#141414" stroke-width="2"/><path d="M3 7l9 6 9-6" fill="none" stroke="#141414" stroke-width="2"/></svg>
      </span>
      <span class="contact-icon" aria-label="Website">
        <svg width="14" height="14" viewBox="0 0 24 24"><circle cx="12" cy="12" r="9" fill="none" stroke="#141414" stroke-width="2"/><path d="M3 12h18M12 3c3 3 3 15 0 18M12 3c-3 3-3 15 0 18" fill="none" stroke="#141414" stroke-width="1.6"/></svg>
      </span>
    </div>
    <ul class="contact-list">
      <li>004790001234</li>
      <li>talmork.llc@postmail.com</li>
      <li>www.talmork.llc</li>
    </ul>
  </section>

  <section class="card card-back">
    <div class="back-brand">TALMORK</div>
    <div class="back-tagline">SINCE 2026</div>
  </section>
</body>
</html>
```